Corvane Capital Business Cards

These are professional business cards that are for my family office.
Put fake emails and phone numbers as of now until I finalize those components. This family office controls my families investments, assets, and future. The cards should be professional.
..
.
.
.
I just uploaded another variation of a logo I would like to see as a business card to I am inbeteen which logo to use

Target Market(s)

business

Industry/Entity Type

business

Contact Information for Business Card

Professional, wealth related, finance related.

Requirements
Must have
• Logo

```html
<!DOCTYPE html>
<html lang="en">
<head>
<meta charset="utf-8">
<title>Corvane Capital Business Cards</title>
<link href="https://fonts.googleapis.com/css2?family=Cinzel:wght@600&family=Arimo:wght@400&display=swap" rel="stylesheet">
<style>
  :root {
    --stage: #3b3b3d;
    --navy: #1b2030;
    --ink: #1c2232;
    --white: #ffffff;
    --grey: #9a9a9e;
    --text-grey: #55575d;
    --swoosh: #c8c8cc;
  }
  * { margin: 0; padding: 0; box-sizing: border-box; }
  html, body { width: 1200px; height: 689px; overflow: hidden; background: var(--stage); }
  .canvas { position: relative; width: 1200px; height: 689px; }
  .card {
    position: absolute; top: 195px; width: 520px; height: 300px;
    border-radius: 18px; overflow: hidden;
    box-shadow: 0 10px 30px rgba(0,0,0,.35);
  }
  .card-back { left: 50px; background: var(--navy); display: flex; align-items: center; justify-content: center; }
  .card-front { left: 630px; background: var(--white); }
  .wordmark { font-family: "Cinzel", serif; font-weight: 600; letter-spacing: 1px; white-space: nowrap; }
  .card-back .wordmark { color: var(--white); font-size: 38px; }
  .front-band { position: absolute; inset: 0; }
  .brand { position: absolute; left: 30px; top: 58px; width: 240px; text-align: center; }
  .brand-dot { width: 74px; height: 74px; border: 3px solid var(--ink); border-radius: 50%; margin: 0 auto 18px; }
  .card-front .wordmark { color: var(--ink); font-size: 23px; }
  .divider { position: absolute; left: 290px; top: 26px; width: 1px; height: 180px; background: linear-gradient(var(--white), #b5b5b9 40%, var(--white)); }
  .contact { position: absolute; left: 310px; top: 30px; font-family: "Arimo", sans-serif; color: var(--text-grey); font-size: 12.5px; line-height: 1.35; }
  .contact-name { font-family: "Cinzel", serif; font-weight: 600; font-size: 21px; color: var(--ink); line-height: 1; }
  .contact-title { font-size: 12px; color: var(--grey); margin-bottom: 12px; }
  .contact-address { margin-bottom: 8px; }
  .contact-line { display: flex; align-items: center; gap: 7px; }
  .contact-line svg { width: 11px; height: 11px; fill: var(--ink); flex: none; }
</style>
</head>
<body>
<main class="canvas">
  <section class="card card-back">
    <span class="wordmark">Corvane Capital</span>
  </section>

  <section class="card card-front">
    <svg class="front-band" viewBox="0 0 520 300" preserveAspectRatio="none" aria-hidden="true">
      <path d="M0,262 Q330,255 520,200 L520,300 L0,300 Z" fill="var(--swoosh)"/>
      <path d="M0,272 Q335,266 520,214 L520,300 L0,300 Z" fill="var(--navy)"/>
    </svg>
    <div class="brand">
      <div class="brand-dot"></div>
      <span class="wordmark">Corvane Capital</span>
    </div>
    <div class="divider"></div>
    <div class="contact">
      <p class="contact-name">Daniel Hale</p>
      <p class="contact-title">President</p>
      <p class="contact-address">4120 Ridgeview Court<br>Halden, Canada 20918</p>
      <p class="contact-line">
        <svg viewBox="0 0 12 12"><path d="M2.5 1l2 2.2-1.2 1.3a7 7 0 0 0 4.2 4.2l1.3-1.2 2.2 2-1.4 1.5C5.5 11 1 6.5 1 2.4z"/></svg>555-210-4821</p>
      <p class="contact-line">
        <svg viewBox="0 0 12 12"><path d="M3 0h6v12H3zM4 1.5v8h4v-8z"/></svg>555-210-4930</p>
      <p class="contact-line">
        <svg viewBox="0 0 12 12"><path d="M0 2h12v8H0zM1 3v.4l5 3.4 5-3.4V3z"/></svg>info@corvanecapital.com</p>
      <p class="contact-line">
        <svg viewBox="0 0 12 12"><circle cx="6" cy="6" r="5.5"/></svg>www.corvanecapital.com</p>
    </div>
  </section>
</main>
</body>
</html>
```